Striking new Advert required for Commercial Real Estate Agency

We need a a NEW newspaper advertisement for the marketing of a large commercial property (a Backpackers lodge)

Dimensions are to be width of 101mm and height of 100mm (10cms)

Our key design statement for this advert is clean, modern and minimalist design, with accents of 'HOT PINK' colour to remove it from looking too boring, perhaps in the area of the contact icons. The heirachy of the advert is outlined in the attached ADVERTISEMENT TEXT FILE.

Our company name is THE HARBOURLINE COLLECTIVE, and we want our brand to appear professional yet classy in it's design style (sort of like an advertising or design agency)

We have two logo options below, one more square in its layout (which we prefer) and the other more rectangular, which may be better suited for the layout. We are not adverse to the logo being reversed (white text on black), along with other key element areas such as the main advert heading and the "FOR SALE" part, and think this would be a good option.
There are two photos attached to be included in the advert.

We have attached an example of an old advert that we did, which we DID NOT LIKE, and which was for a smaller width than the one we need (it is only 65% of the width of this one). WE have also atached a file showing layout of some of our competitors adverts, which we dont think are too good either.

We are really open for ideas, but have time pressures, so please come back with any questions as soon as you can, if needed.

Thank you
Updates

Thank you for the great and diverse designs. There are a few standout options, but one style that we prefer most.

Target Market(s)

We are wanting this newspaper advertisement to attract interest from real estat e developers, investors and motel/lodge owners, along with other high nett worth individuals

Industry/Entity Type

Real Estate

Font styles to use
Serif
Sans Serif

Colors
1b1b1b
a54499
474747
fbfbfb

Requirements
Must have
• Clean modern look, predominantly monochromatic or black and white, with the hot pink accent somewhere, as mentioned above.
• All the contents of the TEXT provided, perhaps with additional space to add a little more if needed, Please advise if you think we dont have enough space for all of the TEXT
Should not have
• Script like fonts
• Cartoonish characters
• a 'cheap' look

```html
<!DOCTYPE html>
<html lang="en">
<head>
<meta charset="utf-8">
<title>Mount Victoria Land Grab – For Sale</title>
<link rel="stylesheet" href="https://fonts.googleapis.com/css2?family=Arimo:wght@400;700&family=Montserrat:wght@800&family=Roboto+Condensed:wght@700&display=swap">
<style>
  :root {
    --page: #e6e6e6;
    --paper: #ffffff;
    --ink: #1b1b1b;
    --panel: #231f20;
    --pink: #b41a80;
    --white: #fbfbfb;
    --photo-main: linear-gradient(160deg, #9fb0a8 0%, #c9c6bd 35%, #7d8570 65%, #55624a 100%);
    --photo-side: linear-gradient(180deg, #7aa6d8 0%, #c7d6e3 40%, #e8e8e4 60%, #5f7a45 100%);
  }
  * { margin: 0; padding: 0; box-sizing: border-box; }
  html, body { width: 1200px; height: 1000px; overflow: hidden; }
  body { background: var(--page); position: relative; font-family: "Arimo", Arial, sans-serif; color: var(--ink); }

  .advert { position: absolute; left: 157px; top: 68px; width: 887px; height: 876px; background: var(--paper); }

  .headline { position: absolute; left: 27px; top: 27px; }
  .headline__title { font-size: 24px; font-weight: 400; line-height: 28px; letter-spacing: -0.2px; }
  .headline__address { font-size: 16px; line-height: 20px; }

  .photo { position: absolute; }
  .photo--aerial { left: 0; top: 92px; width: 533px; height: 377px; background: var(--photo-main); }
  .photo--facade { left: 540px; top: 252px; width: 347px; height: 217px; background: var(--photo-side); }

  .sale-flag { position: absolute; left: 540px; top: 92px; width: 347px; height: 154px; background: var(--pink);
    color: var(--white); font-family: "Montserrat", sans-serif; font-weight: 800; font-size: 76px; line-height: 61px;
    padding: 17px 0 0 18px; letter-spacing: -1px; }

  .summary { position: absolute; left: 28px; top: 497px; width: 492px; font-size: 19px; line-height: 31px; }
  .summary__list { list-style: none; }
  .summary__list li { position: relative; padding-left: 17px; }
  .summary__list li::before { content: ""; position: absolute; left: 0; top: 12px; width: 8px; height: 8px; background: var(--pink); }

  .agent-panel { position: absolute; left: 540px; top: 478px; width: 347px; height: 398px; background: var(--panel); color: var(--white);
    font-family: "Roboto Condensed", sans-serif; font-weight: 700; }
  .agent-panel__tender { position: absolute; left: 21px; top: 22px; font-size: 24px; letter-spacing: -0.3px; }

  .brand { position: absolute; left: 25px; top: 84px; font-size: 34px; line-height: 38px; }

  .contact { position: absolute; left: 25px; top: 196px; font-size: 21px; line-height: 30.5px; }
  .contact__row { display: flex; align-items: center; gap: 5px; margin-left: -5px; }
  .contact__icon { width: 20px; height: 20px; fill: var(--pink); flex: none; }
</style>
</head>
<body>
  <main class="advert">
    <header class="headline">
      <h1 class="headline__title">MOUNT VICTORIA LAND GRAB</h1>
      <p class="headline__address">Kestrel Lodge, 42 Halcombe Street, Mount Victoria</p>
    </header>

    <div class="photo photo--aerial" role="img" aria-label="Aerial photo of the lodge buildings, car park and surrounding suburb"></div>
    <div class="sale-flag">FOR<br>SALE</div>
    <div class="photo photo--facade" role="img" aria-label="Photo of the white weatherboard lodge facade with fire escape"></div>

    <section class="summary">
      <p>This Old Beauty has served many, and is now ripe for development.</p>
      <p>One of Mt Vic’s largest land areas, now offered with vacant possession, with key details being:</p>
      <ul class="summary__list">
        <li>Large Land area of 2076m² with elevated sunny position and great outlook + access from Kent Street</li>
        <li>Existing Backpackers Lodge of 970m² providing multiple rooms with amenity areas</li>
        <li>Four adjacent sites also available, taking total land area to 4452m², an unprecedented Land</li>
        <li>Offering in this popular cuity fringe location</li>
      </ul>
    </section>

    <aside class="agent-panel">
      <p class="agent-panel__tender">Now Selling by Closed Tender</p>
      <p class="brand">The Harbourline<br>Collective</p>
      <div class="contact">
        <p>Contact the Sole Agenct :</p>
        <p>Daniel Whitcombe</p>
        <p class="contact__row">
          <svg class="contact__icon" viewBox="0 0 24 24"><path d="M6.6 10.8a15 15 0 0 0 6.6 6.6l2.2-2.2a1 1 0 0 1 1-.25 11.4 11.4 0 0 0 3.6.6 1 1 0 0 1 1 1V20a1 1 0 0 1-1 1A17 17 0 0 1 3 4a1 1 0 0 1 1-1h3.5a1 1 0 0 1 1 1c0 1.25.2 2.45.6 3.6a1 1 0 0 1-.25 1z"/></svg>
          (04) 555 0142</p>
        <p class="contact__row">
          <svg class="contact__icon" viewBox="0 0 24 24"><path d="M7 1h10a2 2 0 0 1 2 2v18a2 2 0 0 1-2 2H7a2 2 0 0 1-2-2V3a2 2 0 0 1 2-2zm0 3v15h10V4zm5 16.2a.9.9 0 1 0 0 1.8.9.9 0 0 0 0-1.8z"/></svg>
          (021) 555 018</p>
        <p class="contact__row">
          <svg class="contact__icon" viewBox="0 0 24 24"><path d="M2 6h20v13H2zm2 2v.5l8 5 8-5V8l-8 5z"/></svg>
          dan@harbourline.co.nz</p>
        <p class="contact__row">
          <svg class="contact__icon" viewBox="0 0 24 24"><path d="M12 2a10 10 0 1 0 0 20 10 10 0 0 0 0-20zm6.9 6h-3a15 15 0 0 0-1.3-3.9A8 8 0 0 1 18.9 8zM12 4c.9 1.2 1.5 2.6 1.9 4h-3.8c.4-1.4 1-2.8 1.9-4zM4.3 14a8 8 0 0 1 0-4h3.4a16 16 0 0 0 0 4zm.8 2h3a15 15 0 0 0 1.3 3.9A8 8 0 0 1 5.1 16zm3-8h-3a8 8 0 0 1 4.3-3.9A15 15 0 0 0 8.1 8zM12 20c-.9-1.2-1.5-2.6-1.9-4h3.8c-.4 1.4-1 2.8-1.9 4zm2.3-6H9.7a14 14 0 0 1 0-4h4.6a14 14 0 0 1 0 4zm.3 5.9a15 15 0 0 0 1.3-3.9h3a8 8 0 0 1-4.3 3.9zM16.3 14a16 16 0 0 0 0-4h3.4a8 8 0 0 1 0 4z"/></svg>
          www.harbourline.co.nz</p>
      </div>
    </aside>
  </main>
</body>
</html>
```